Boutique Store Selling Antiques and Unique Finds

I need a Web Page designed for my Store Called "Willow Lane". I would like a very classic, muted design that looks European when pulled up. I will be selling Antiques from all over the world and Unique finds that have reproduced. I will also be selling high-end purses and jewelry with unique, reasonable products for the every-day buyer as well.

Target Market(s)

25-70 year old men and women;)

Coding

Coded - Design and coding required

Number of Pages Required

1 page

Colors

Designer to choose only greyscale colors for use in the design.

Requirements
Must have
• I want it

```html
<!DOCTYPE html>
<html lang="en">
<head>
<meta charset="utf-8">
<title>Willow Lane — Antiques &amp; Unique Finds</title>
<link href="https://fonts.googleapis.com/css2?family=Cinzel:wght@400;600&family=Roboto:wght@400;500;700&display=swap" rel="stylesheet">
<style>
:root{
  --page:#f6f1eb;
  --topbar:#e1dbd7;
  --band:#dcd5d1;
  --ink:#1c1a19;
  --muted:#6b6663;
  --soft:#8d8885;
  --card:#ffffff;
  --line:#e4dfdb;
  --black:#121212;
}
*{box-sizing:border-box;margin:0;padding:0}
html,body{width:1200px;height:4054px;overflow:hidden}
body{position:relative;background:var(--page);font-family:"Roboto",Arial,sans-serif;color:var(--ink)}
.abs{position:absolute}
.serif{font-family:"Cinzel",Georgia,serif}
a{color:inherit;text-decoration:none}

/* top bar */
.topbar{left:0;top:0;width:1200px;height:40px;background:var(--topbar);font-size:14px;color:var(--muted)}
.menu-icon{left:112px;top:12px}
.topbar .divider{left:151px;top:8px;width:1px;height:24px;background:#999}
.search{left:170px;top:11px;display:flex;align-items:center;gap:12px;color:var(--ink)}
.account{left:836px;top:11px;display:flex;align-items:center;gap:6px}
.cart{left:1010px;top:11px;display:flex;align-items:center;gap:8px}

/* header */
.brand{left:0;top:88px;width:1200px;text-align:center;font-size:27px;letter-spacing:4px;color:var(--ink)}
.nav{left:110px;top:149px;display:flex;gap:0;font-size:15px;font-weight:500}
.nav a{margin-right:31px}
.nav a:last-child{margin-right:0}

/* hero */
.hero{left:0;top:181px;width:1200px;height:580px;background:linear-gradient(90deg,#e9e3dd 0%,#ddd6d0 45%,#b9aea3 70%,#cfc6bd 100%)}
.hero-title{left:110px;top:377px;font-size:37px;letter-spacing:5px;font-weight:600}
.hero-text{left:110px;top:443px;width:470px;font-size:14.5px;line-height:27px;color:#3a3634}
.btn{background:var(--black);color:#fff;font-weight:700;font-size:15.5px;display:flex;align-items:center;justify-content:center}
.hero-btn{left:110px;top:515px;width:142px;height:42px}

/* section titles */
.section-title{left:0;width:1200px;text-align:center;font-size:34px;letter-spacing:4px;font-weight:600}

/* product cards */
.card{background:var(--card);box-shadow:0 1px 3px rgba(0,0,0,.08);text-align:center}
.card .photo{width:100%}
.card .name{font-size:16.5px;font-weight:500;margin-top:29px}
.card .price{font-size:16.5px;font-weight:700;margin-top:12px}

/* new arrival */
.arrival-box{left:425px;top:2458px;width:351px;height:126px;background:#fff;box-shadow:0 4px 6px rgba(0,0,0,.2);text-align:center}
.arrival-box h3{font-size:27px;letter-spacing:3px;font-weight:600;margin-top:20px}
.arrival-box p{font-size:17px;font-weight:500;margin-top:8px}

/* antiques */
.caption{font-size:21px;font-weight:500}

/* newsletter */
.newsletter{left:0;top:3567px;width:1200px;height:142px;background:var(--band)}
.news-intro{left:110px;top:3611px;font-size:15px;color:#333}
.news-title{left:110px;top:3636px;font-size:22px;letter-spacing:2px;font-weight:600}
.email{left:584px;top:3614px;width:306px;height:47px;background:#fff;display:flex;align-items:center;gap:8px;padding-left:20px;font-size:13px;color:#999}
.submit{left:910px;top:3614px;width:144px;height:47px}

/* footer */
.foot-col{top:3786px}
.foot-col h4{font-size:16px;font-weight:500;letter-spacing:.5px;margin-bottom:13px}
.foot-col li{list-style:none;font-size:12px;color:var(--muted);line-height:22px}
.foot-rule{top:3800px;width:1px;height:135px;background:var(--line)}
.contact li{display:flex;gap:14px;align-items:flex-start;margin-bottom:6px;line-height:15px}
.follow li{display:flex;align-items:center;gap:14px;margin-bottom:8px}
.follow .dot{width:26px;height:26px;border-radius:50%;background:#ebe6e2}
.copyright{left:0;top:4004px;width:1200px;text-align:center;font-size:11px;color:var(--muted)}
.pay{left:930px;top:4000px;display:flex;gap:4px}
.pay span{height:18px;padding:0 4px;background:#d8d2ce;font-size:9px;color:#333;display:flex;align-items:center}
</style>
</head>
<body>

<div class="abs topbar">
  <svg class="abs menu-icon" width="24" height="16" viewBox="0 0 24 16"><path d="M0 1h24M0 8h24M0 15h24" stroke="#333" stroke-width="1.6"/></svg>
  <span class="abs divider"></span>
  <div class="abs search">
    <svg width="14" height="14" viewBox="0 0 14 14"><circle cx="6" cy="6" r="4.5" fill="none" stroke="#111" stroke-width="2"/><path d="M9.5 9.5L13 13" stroke="#111" stroke-width="2"/></svg>
    <span>Search enter keyword</span>
  </div>
  <div class="abs account">
    <svg width="12" height="13" viewBox="0 0 12 13"><circle cx="6" cy="4" r="3" fill="none" stroke="#888"/><path d="M1 12.5c0-3 2.2-5 5-5s5 2 5 5z" fill="none" stroke="#888"/></svg>
    <span>Sign in &nbsp;or&nbsp; Register</span>
  </div>
  <div class="abs cart">
    <svg width="15" height="13" viewBox="0 0 15 13"><path d="M0 1h3l2 8h8l2-6H4" fill="none" stroke="#777" stroke-width="1.6"/><circle cx="6" cy="11.5" r="1.3" fill="#777"/><circle cx="12" cy="11.5" r="1.3" fill="#777"/></svg>
    <span>(0)items</span>
  </div>
</div>

<div class="abs brand serif">Willow Lane</div>
<nav class="abs nav">
  <a href="#">Home</a><a href="#">Sale</a><a href="#">Shop Online</a><a href="#">Antiques And Unique</a><a href="#">High-end Purses</a><a href="#">Jewelry</a><a href="#">Gift Vouchers</a><a href="#">Events</a><a href="#">About</a><a href="#">Contact</a>
</nav>

<section class="abs hero" role="img" aria-label="Gilded antique crown resting on a stack of old leather-bound books"></section>
<h1 class="abs hero-title serif">Willow Lane</h1>
<p class="abs hero-text">Sed ut perspiciatis unde omnis iste natus error sit voluptatem accusantium doloremque laudantium</p>
<a class="abs btn hero-btn" href="#">SHOP NOW</a>

<h2 class="abs section-title serif" style="top:872px">Shop Online</h2>

<div class="abs card" style="left:55px;top:964px;width:538px;height:532px">
  <div class="photo" role="img" aria-label="Jewelled antique crown on a dark pedestal" style="height:427px;background:linear-gradient(180deg,#6d5a45,#b19a7c 45%,#4b4642)"></div>
  <p class="name">Lorem ipsum dolor sit amet</p><p class="price">$ 275.00</p>
</div>
<div class="abs card" style="left:608px;top:964px;width:537px;height:532px">
  <div class="photo" role="img" aria-label="Red leather journal with compass, hourglass and small trinkets" style="height:427px;background:linear-gradient(135deg,#d9c9b5,#8a4f3a 45%,#9b7a5b)"></div>
  <p class="name">Lorem ipsum dolor sit amet</p><p class="price">$ 275.00</p>
</div>

<div class="abs card" style="left:55px;top:1532px;width:353px;height:460px">
  <div class="photo" role="img" aria-label="Antique roll-top desk with blue and white porcelain plates" style="height:358px;background:linear-gradient(180deg,#5a3c2a,#8e4e2c 50%,#c9c3c8)"></div>
  <p class="name">Lorem ipsum dolor sit amet</p><p class="price">$ 275.00</p>
</div>
<div class="abs card" style="left:422px;top:1532px;width:353px;height:460px">
  <div class="photo" role="img" aria-label="Gilded crown on a stack of leather-bound books" style="height:358px;background:linear-gradient(180deg,#d8d1cb,#8f7a58 55%,#5c4a3a)"></div>
  <p class="name">Lorem ipsum dolor sit amet</p><p class="price">$ 275.00</p>
</div>
<div class="abs card" style="left:789px;top:1532px;width:353px;height:460px">
  <div class="photo" role="img" aria-label="Tufted tan wingback armchair in a bright room" style="height:358px;background:linear-gradient(180deg,#f2f0ee,#c4a384 55%,#e9e7e5)"></div>
  <p class="name">Lorem ipsum dolor sit amet</p><p class="price">$ 275.00</p>
</div>

<div class="abs" role="img" aria-label="Brown leather purse on a wooden table" style="left:0;top:2096px;width:595px;height:556px;background:linear-gradient(160deg,#7d5a45,#5e3c30 50%,#8a6a4f)"></div>
<div class="abs" role="img" aria-label="Ornate jewelled crown with coloured stones" style="left:603px;top:2096px;width:597px;height:556px;background:linear-gradient(180deg,#b9afa3,#6a5536 50%,#2e2a27)"></div>
<div class="abs arrival-box">
  <h3 class="serif">New Arival</h3>
  <p>Purses &nbsp;&nbsp;&nbsp; | &nbsp;&nbsp;&nbsp; Jewelry</p>
</div>

<div class="abs" role="img" aria-label="Blue and white porcelain vases" style="left:52px;top:2762px;width:510px;height:640px;background:linear-gradient(180deg,#1f2e52,#5a6f9c 50%,#1b2542)"></div>
<h2 class="abs serif" style="left:600px;top:2884px;width:570px;text-align:center;font-size:34px;letter-spacing:3px;font-weight:600">Antiques &amp; Unique</h2>
<a class="abs btn" href="#" style="left:816px;top:2956px;width:140px;height:41px">SHOP NOW</a>
<div class="abs" role="img" aria-label="Engraved silver coffee pot on a silver tray" style="left:638px;top:3104px;width:510px;height:298px;background:linear-gradient(135deg,#5a4a40,#a69f98 45%,#4a3a30)"></div>
<p class="abs caption" style="left:74px;top:3434px">Lorem ipsum dolor sit consectetur</p>
<p class="abs caption" style="left:660px;top:3434px">Lorem ipsum dolor sit consectetur</p>

<section class="abs newsletter"></section>
<p class="abs news-intro">Subscribe Our newsletter to get latest updates</p>
<p class="abs news-title serif">Sign Up To Our Newsletter</p>
<div class="abs email">
  <svg width="12" height="9" viewBox="0 0 12 9"><rect width="12" height="9" fill="#aaa"/><path d="M0 0l6 5 6-5" stroke="#fff" fill="none"/></svg>
  Your Email Address
</div>
<a class="abs btn submit" href="#">SUBMIT</a>

<div class="abs foot-col" style="left:113px">
  <h4>QUICK LINKS</h4>
  <ul><li>Home</li><li>Sale</li><li>Shop Online</li><li>Antiques And Unique</li><li>High-end Purses</li><li>Jewelry</li></ul>
</div>
<span class="abs foot-rule" style="left:272px"></span>
<div class="abs foot-col" style="left:350px">
  <h4>INFORMATION</h4>
  <ul><li>Terms &amp; Conditions</li><li>Privacy Policy</li><li>Disclaimer</li><li>Site Map</li><li>Contact Us</li><li>Categories</li></ul>
</div>
<span class="abs foot-rule" style="left:537px"></span>
<div class="abs foot-col contact" style="left:614px">
  <h4>CONTACT INFO</h4>
  <ul>
    <li><svg width="12" height="12" viewBox="0 0 12 12"><path d="M1 5c0-3 10-3 10 0v2H8V5H4v2H1z M3 8h6v3H3z" fill="#333"/></svg>(215) 555-0142</li>
    <li><svg width="12" height="12" viewBox="0 0 12 12"><rect x="3" y="1" width="6" height="3" fill="#333"/><rect x="1" y="4" width="10" height="5" fill="#333"/><rect x="3" y="8" width="6" height="3" fill="#777"/></svg>(215) 555-0142</li>
    <li><svg width="12" height="12" viewBox="0 0 12 12"><rect y="2" width="12" height="8" fill="#333"/><path d="M0 2l6 4 6-4" stroke="#fff" fill="none"/></svg><span style="text-decoration:underline">info@WillowLane.com</span></li>
    <li><svg width="12" height="13" viewBox="0 0 12 13"><path d="M6 12C2 7 2 6 2 4.5a4 4 0 018 0C10 6 10 7 6 12z" fill="#333"/><circle cx="6" cy="4.5" r="1.4" fill="#fff"/></svg>#2868 Lorem ipsum dolor sit<br>amet, consectetur</li>
  </ul>
</div>
<span class="abs foot-rule" style="left:876px"></span>
<div class="abs foot-col follow" style="left:953px">
  <h4>FOLLOW US</h4>
  <ul>
    <li><span class="dot"></span>Friendbook</li>
    <li><span class="dot"></span>Chirper</li>
    <li><span class="dot"></span>Circles</li>
    <li><span class="dot"></span>WorkLink</li>
  </ul>
</div>

<p class="abs copyright">Copyrights © Willow Lane 2021 | Allrights Reserved</p>
<div class="abs pay"><span>Paycard</span><span>Coinline</span><span>Tallymark</span><span>Brightpay</span><span>Bank</span></div>

</body>
</html>
```